Freelance business trainer needs a new business card

My business is called Brontlearn. I provide training in the workplace on management, coaching and mentoring, and customer service topics for a variety of businesses, colleges and private training providers, and teach on management programs. I need a professional but eye catching business card. Business colours grey and orange. My name Marion Tadwick; Tel 07382 415067; email mtadwick@brontlearn.co.uk; website www.brontlearn.co.uk.
Happy to have some sort of logo on front and details on back or all on one side
Target Market(s)
SME businesses and colleges - workshops i run are for adults in the workplace
Industry/Entity Type
Training
Look and feel

```html
<!DOCTYPE html>
<html lang="en">
<head>
<meta charset="utf-8">
<title>Brontlearn – Business Card</title>
<link rel="stylesheet" href="https://fonts.googleapis.com/css2?family=Poppins:wght@400;600;700&display=swap">
<style>
  :root {
    --orange: #f08c1e;
    --orange-deep: #d8701a;
    --orange-light: #f7a23a;
    --charcoal: #3d3a3a;
    --charcoal-dark: #2f2c2c;
    --white: #ffffff;
    --stage: #262626;
    --font: "Poppins", "Century Gothic", sans-serif;
  }
  * { box-sizing: border-box; margin: 0; padding: 0; }
  html, body {
    width: 1200px; height: 900px; overflow: hidden;
    background: var(--stage);
    font-family: var(--font);
  }
  .canvas { position: relative; width: 1200px; height: 900px; }

  .card {
    position: absolute; left: 285px; width: 630px; height: 360px;
    overflow: hidden; border-radius: 2px;
    box-shadow: 0 10px 30px rgba(0,0,0,.45);
  }
  .card--details { top: 60px; background: var(--orange); }
  .card--front {
    top: 480px;
    background: radial-gradient(ellipse at 30% 25%, var(--orange-light) 0%, var(--orange) 45%, var(--orange-deep) 100%);
  }

  /* details side */
  .white-band { position: absolute; left: 0; top: 0; width: 100%; height: 100px; background: var(--white); }
  .brand-name {
    position: absolute; left: 40px; top: 40px;
    font-weight: 700; font-size: 44px; line-height: 1; letter-spacing: -0.5px;
    color: var(--charcoal);
  }
  .tagline-band {
    position: absolute; left: 40px; top: 100px; height: 22px; padding: 0 12px;
    background: var(--charcoal); color: var(--white);
    font-weight: 600; font-size: 11px; line-height: 22px; white-space: nowrap;
  }
  .tagline-band::after {
    content: ""; position: absolute; left: 16px; top: 22px;
    border-left: 8px solid transparent; border-right: 8px solid transparent;
    border-top: 8px solid var(--charcoal);
  }
  .person { position: absolute; left: 56px; top: 140px; color: var(--white); }
  .person-name { font-weight: 700; font-size: 17px; line-height: 1.2; }
  .person-role, .person-credentials { font-size: 11.5px; line-height: 1.45; }
  .specialism { margin-top: 12px; }
  .specialism-title { font-weight: 700; font-size: 14px; color: var(--charcoal); line-height: 1.4; }
  .specialism-list { list-style: none; font-size: 15px; line-height: 1.4; color: var(--white); }

  .contact { position: absolute; right: 28px; top: 112px; display: grid; grid-template-columns: auto 22px; gap: 8px 12px; align-items: center; }
  .contact-text { font-size: 12px; color: var(--white); text-align: right; }
  .contact-icon { width: 22px; height: 22px; background: var(--charcoal); display: flex; align-items: center; justify-content: center; }

  .footer-band {
    position: absolute; left: 0; bottom: 0; width: 100%; height: 60px;
    background: var(--charcoal);
    display: flex; align-items: center; justify-content: flex-end; padding-right: 70px;
  }
  .website { color: var(--white); font-weight: 600; font-size: 17px; letter-spacing: 5px; }

  /* front side */
  .front-band { position: absolute; left: 0; bottom: 0; width: 100%; height: 70px; background: var(--charcoal-dark); }
  .front-lockup { position: absolute; left: 0; top: 78px; width: 100%; text-align: center; }
  .front-lockup .brand-name { position: static; font-size: 66px; display: inline-block; }
  .front-lockup .tagline {
    display: block; margin-top: 10px;
    font-weight: 600; font-size: 15px; color: var(--charcoal);
  }
</style>
</head>
<body>
<main class="canvas">

  <section class="card card--details" aria-label="Business card, details side">
    <div class="white-band"></div>
    <div class="brand-name">Brontlearn</div>
    <div class="tagline-band">Professional Workplace Training Services</div>

    <div class="person">
      <p class="person-name">Marion Tadwick</p>
      <p class="person-role">Owner/Lead Trainer</p>
      <p class="person-credentials">MCMI, MIFL, CertEd, PGCCM, TIOSH</p>
      <div class="specialism">
        <p class="specialism-title">Specialist areas</p>
        <ul class="specialism-list">
          <li>Customer Service,</li>
          <li>Health and Safety,</li>
          <li>Management &amp; Business.</li>
        </ul>
      </div>
    </div>

    <div class="contact">
      <span class="contact-text">07382 415067</span>
      <span class="contact-icon">
        <svg width="12" height="14" viewBox="0 0 12 14" aria-hidden="true"><rect x="1.5" y="1" width="9" height="12" rx="1" fill="none" stroke="#fff" stroke-width="1.3"/></svg>
      </span>
      <span class="contact-text">mtadwick@brontlearn.co.uk</span>
      <span class="contact-icon">
        <svg width="14" height="10" viewBox="0 0 14 10" aria-hidden="true"><rect x="0.5" y="0.5" width="13" height="9" fill="#fff"/><path d="M0.5 0.5 L7 6 L13.5 0.5" fill="none" stroke="#3d3a3a" stroke-width="1"/></svg>
      </span>
    </div>

    <div class="footer-band"><span class="website">www.brontlearn.co.uk.</span></div>
  </section>

  <section class="card card--front" aria-label="Business card, front side">
    <div class="front-lockup">
      <span class="brand-name">Brontlearn</span>
      <span class="tagline">Professional Workplace Training Services</span>
    </div>
    <div class="front-band"></div>
  </section>

</main>
</body>
</html>
```